Polished Comb salon has created a lotion and needs help titling.Tides by polished comb ?Polis

The product is for a lotion bottle , my prototype lotion bottle size is an 8oz black lotion bottle with pump. I want the label in florescent green. It should tap into the emotion of potential buyers. The design should say choose me 😀(not literally ). Though the text should be clear and punchy . I.e " the skin multi-vitamin." I'm looking for a designer intrigued by the thought of my lotion. The label should be georgeous,informative, with visuals that immediately convey what my product is and how it works.Not distracting, but clear and punchy, with no expectation of someone to read more than a couple of words.The text should support the visual in a way the visual could not. It seems that nowadays visuals are taking over with very little text. The font,color , or punch of color should be enticing.
So here are some particular ideas of points about the lotion that could possibly be put on back as is done by lotion makers.
.ingredients
.TSA approved
.portion of proceeds go to lunch for little ones
.TC circled ( which is for pending trademark)
. I would like the word New in fluorescent on the bottle
.P.O Box address of place of manufacturing product.
. To help skin stay slightly moist,soft,and flexible with a smooth fine grained texture.

Target Market(s)

its a lotion so I want it available for all

Industry/Entity Type

Barber

Colors
9bcb3c

Requirements
Must have
• the word" Tides" and By polished comb...the word new on the bottle visible

```html
<!DOCTYPE html>
<html lang="en">
<head>
<meta charset="UTF-8">
<title>Tides by Polished Comb – Lotion Label</title>
<link rel="stylesheet" href="https://fonts.googleapis.com/css2?family=Montserrat:wght@300;700&display=swap">
<style>
  :root {
    --backdrop: #efefed;
    --label-green: #9bcb3c;
    --label-green-deep: #93c334;
    --panel-white: #ffffff;
    --text-green: #86b82a;
    --text-white: #ffffff;
    --text-dark: #4a4a4a;
  }
  * { margin: 0; padding: 0; box-sizing: border-box; }
  html, body {
    width: 1000px;
    height: 1200px;
    overflow: hidden;
    background: var(--backdrop);
    font-family: "Montserrat", sans-serif;
  }
  .label {
    position: absolute;
    left: 200px;
    top: 130px;
    width: 600px;
    height: 940px;
    background: linear-gradient(180deg, var(--label-green) 0%, var(--label-green-deep) 100%);
    border-radius: 18px;
    overflow: hidden;
  }
  .new-flag {
    position: absolute;
    left: 60px;
    top: 150px;
    padding: 8px 22px;
    border: 3px solid var(--text-white);
    border-radius: 30px;
    font-weight: 700;
    font-size: 26px;
    letter-spacing: 4px;
    color: var(--text-white);
    text-transform: uppercase;
  }
  .brand {
    position: absolute;
    left: 60px;
    top: 230px;
    width: 480px;
  }
  .brand-row {
    display: flex;
    align-items: center;
    gap: 18px;
  }
  .brand-name {
    font-weight: 300;
    font-size: 150px;
    line-height: 1;
    letter-spacing: -4px;
    color: var(--text-white);
  }
  .brand-dot {
    width: 46px;
    height: 46px;
    border-radius: 50%;
    background: var(--text-white);
    margin-top: -40px;
  }
  .brand-by {
    margin-top: 6px;
    margin-left: 4px;
    font-weight: 700;
    font-size: 22px;
    letter-spacing: 0.5px;
    color: var(--text-white);
    text-transform: uppercase;
  }
  .info-panel {
    position: absolute;
    left: 0;
    right: 0;
    top: 480px;
    bottom: 0;
    background: var(--panel-white);
    border-radius: 80px 80px 0 0;
    text-align: center;
    padding: 50px 50px 0;
  }
  .tagline {
    font-weight: 700;
    font-size: 30px;
    color: var(--text-green);
    text-transform: uppercase;
  }
  .description {
    margin: 40px auto 0;
    width: 420px;
    font-weight: 700;
    font-size: 16px;
    line-height: 1.45;
    color: var(--text-green);
    text-align: justify;
    text-align-last: center;
  }
  .benefit {
    margin-top: 52px;
    font-weight: 700;
    font-size: 30px;
    line-height: 1.5;
    color: var(--text-green);
    text-transform: uppercase;
  }
  .net-weight {
    margin-top: 40px;
    font-weight: 700;
    font-size: 24px;
    color: var(--text-dark);
  }
</style>
</head>
<body>
  <main class="label">
    <span class="new-flag">New</span>
    <div class="brand">
      <div class="brand-row">
        <span class="brand-name">Tides</span>
        <span class="brand-dot"></span>
      </div>
      <p class="brand-by">By Polished Comb</p>
    </div>
    <section class="info-panel">
      <h1 class="tagline">The Skin Multi-Vitamin</h1>
      <p class="description">Lorem ipsum dolor sit amet, consectetur adipisicing elit, sed do eiusmod tempor incididunt ut labore et dolore magna aliqua.</p>
      <p class="benefit">Keeps skin soft,<br>smooth and slightly moist</p>
      <p class="net-weight">Net Weight: 8oz</p>
    </section>
  </main>
</body>
</html>
```